I need a new business card designed, we recently rebranded and I need to get a fresh design to match our new logo, colours and branding.

Details:

Derek Havill | Founder & CEO
Address: 7 Marlowfern Lane, #09-14 Tavenport Crest, Singapore 318547
Tel: +65 93568214
Web: www.frostkarta.com.sg
hello@frostkarta.com.sg

I've attached my old card as well

Industry/Entity Type

Business

Requirements
Must have
• Front and Back
Interesting use of logo
Correct use of colour scheme

```html
<!DOCTYPE html>
<html lang="en">
<head>
<meta charset="utf-8">
<title>Frostkarta Business Card – Front and Back</title>
<link rel="stylesheet" href="https://fonts.googleapis.com/css2?family=Arimo:wght@400;700&family=Russo+One&display=swap">
<style>
  :root {
    --stage: #000000;
    --card: #ffffff;
    --brand-blue: #1b95d3;
    --title-grey: #b3b3b3;
    --label-grey: #6e6e6e;
    --on-blue: #ffffff;
  }
  * { margin: 0; padding: 0; box-sizing: border-box; }
  html, body { width: 1200px; height: 1000px; overflow: hidden; background: var(--stage); }
  .stage { position: relative; width: 1200px; height: 1000px; font-family: "Arimo", Arial, sans-serif; }

  .side-label { position: absolute; color: var(--label-grey); font-size: 22px; }
  .side-label--front { left: 137px; top: 96px; }
  .side-label--back { left: 662px; top: 104px; }

  .card { position: absolute; top: 147px; width: 424px; height: 737px; background: var(--card); overflow: hidden; }
  .card--front { left: 139px; }
  .card--back { left: 664px; }

  .brand { position: absolute; display: flex; align-items: center; }
  .brand__mark { background: var(--brand-blue); flex: none; }
  .brand__name { color: var(--brand-blue); font-weight: 400; line-height: 1; white-space: nowrap; }

  .brand--front { left: 36px; top: 30px; }
  .brand--front .brand__mark { width: 64px; height: 64px; margin-right: 16px; }
  .brand--front .brand__name { font-size: 42px; }

  .brand--back { left: 132px; top: 346px; }
  .brand--back .brand__mark { width: 40px; height: 40px; margin-right: 10px; }
  .brand--back .brand__name { font-size: 26px; }

  .holder { position: absolute; left: 37px; top: 345px; font-family: "Russo One", "Arimo", sans-serif; }
  .holder__name { color: var(--brand-blue); font-size: 40px; font-weight: 400; line-height: 1; text-transform: uppercase; }
  .holder__title { color: var(--title-grey); font-size: 23px; line-height: 1; margin-top: 8px; text-transform: uppercase; }

  .contact-band { position: absolute; left: 0; top: 472px; width: 424px; height: 265px; background: var(--brand-blue); color: var(--on-blue); }
  .contact-list { position: absolute; left: 38px; top: 27px; font-size: 20px; line-height: 30px; }
  .contact-row { display: grid; grid-template-columns: 83px 24px auto; }
  .contact-row--gap { margin-top: 30px; }
</style>
</head>
<body>
<main class="stage">
  <p class="side-label side-label--front">Front</p>
  <p class="side-label side-label--back">Back</p>

  <section class="card card--front" aria-label="Card front">
    <div class="brand brand--front">
      <span class="brand__mark"></span>
      <span class="brand__name">frostkarta</span>
    </div>

    <div class="holder">
      <h1 class="holder__name">Derek Havill</h1>
      <p class="holder__title">Founder &amp; CEO</p>
    </div>

    <div class="contact-band">
      <div class="contact-list">
        <div class="contact-row"><span>Tel</span><span>:</span><span>+65 93568214</span></div>
        <div class="contact-row"><span>Web</span><span>:</span><span>www.frostkarta.com.sg</span></div>
        <div class="contact-row"><span>e-mail</span><span>:</span><span>hello@frostkarta.com.sg</span></div>
        <div class="contact-row contact-row--gap"><span>Address</span><span>:</span><span>7 Marlowfern Lane,<br>#09-14 Tavenport Crest,<br>Singapore 318547</span></div>
      </div>
    </div>
  </section>

  <section class="card card--back" aria-label="Card back">
    <div class="brand brand--back">
      <span class="brand__mark"></span>
      <span class="brand__name">frostkarta</span>
    </div>
  </section>
</main>
</body>
</html>
```